RW Holloway LLC Business Card - Civil Engineering & Consulting Firm

We need a Business Card that is elegant, and masculine.  It is our Professional Civil Engineering & Consulting Company located in San Antonio TX (Not s construction or builder firm- no gears & no tool images please). We provide civil engineering services including  commercial site plans, grading and drainage plans, utility plans, hydraulics and hydrology, land planning, utility coordination, and other general civil engineering services related to commercial and residential development.
We have 2 existing Logos. We would like to convey reliability, strength, trustworthiness and attention to detail.  Blues and orange tones as per logo We are OK with the use of a darker blue in the mix.  We have 2 logo versions - Full Company Name Logo to go on the back of card, & Small Icon Logo for the front w/ personal Info.

Target Market(s)
Architects, Real Estate Developers, Other Strctural Engineers, Surveyers, General Contractors
Industry/Entity Type
Professional Civil Engineering
Contact Information for Business Card
Name, Position, Address, Cell & Office #, email, and company website
Font styles to use
Other font styles liked:
- Avian
Requirements
Should not have
- No Tools, No Gears, no Cranes, or Construction Equipment.

```html
<!DOCTYPE html>
<html lang="en">
<head>
<meta charset="utf-8">
<title>RW Holloway LLC – Business Card</title>
<link href="https://fonts.googleapis.com/css2?family=Montserrat:wght@300;400;700&display=swap" rel="stylesheet">
<style>
  :root {
    --sky: #7aaed8;
    --sky-mid: #a6b4c0;
    --amber: #e8923a;
    --amber-soft: #d9a273;
    --white: #ffffff;
    --paper: #f3f3f4;
    --stage: #9a9a9a;
    --ink-light: #ffffff;
  }
  * { box-sizing: border-box; margin: 0; padding: 0; }
  html, body { width: 1200px; height: 900px; overflow: hidden; }
  body {
    background: var(--stage);
    font-family: "Montserrat", sans-serif;
    position: relative;
  }
  .card {
    position: absolute;
    width: 620px;
    height: 354px;
    border-radius: 30px;
    overflow: hidden;
  }
  /* Brand side */
  .card--brand {
    left: 90px;
    top: 70px;
    background: linear-gradient(155deg, var(--sky) 0%, var(--sky-mid) 38%, var(--amber-soft) 62%, var(--amber) 100%);
    display: flex;
    align-items: center;
    justify-content: center;
  }
  .brand-name {
    color: var(--ink-light);
    font-weight: 300;
    font-size: 46px;
    letter-spacing: 4px;
    text-transform: uppercase;
  }
  /* Contact side */
  .card--contact {
    left: 490px;
    top: 476px;
    background: linear-gradient(180deg, var(--white) 0%, var(--paper) 100%);
  }
  .card-waves { position: absolute; inset: 0; width: 100%; height: 100%; }
  .contact-brand {
    position: absolute;
    right: 48px;
    top: 40px;
    color: var(--sky);
    font-weight: 700;
    font-size: 20px;
    letter-spacing: 1px;
  }
  .contact-details {
    position: absolute;
    left: 64px;
    top: 186px;
    color: var(--ink-light);
    font-size: 13px;
    line-height: 17px;
    font-weight: 400;
  }
  .person-name { font-weight: 700; font-size: 15px; letter-spacing: 0.5px; text-transform: uppercase; }
  .person-role { font-size: 14px; margin-bottom: 6px; }
  .address { margin-bottom: 4px; }
  .contact-line { display: flex; align-items: center; gap: 8px; }
  .contact-line svg { width: 13px; height: 13px; flex: none; }
</style>
</head>
<body>

<section class="card card--brand">
  <h1 class="brand-name">RW Holloway LLC</h1>
</section>

<section class="card card--contact">
  <svg class="card-waves" viewBox="0 0 620 354" preserveAspectRatio="none" aria-hidden="true">
    <defs>
      <linearGradient id="contactFill" x1="0" y1="0.2" x2="1" y2="0.8">
        <stop offset="0" stop-color="#7aaed8"/>
        <stop offset="0.45" stop-color="#b4afa6"/>
        <stop offset="1" stop-color="#e8923a"/>
      </linearGradient>
    </defs>
    <path d="M0,128 C120,100 260,108 360,110 C470,113 570,102 620,72" fill="none" stroke="#e8923a" stroke-width="5"/>
    <path d="M0,144 C120,116 260,122 360,124 C470,127 575,114 620,90 L620,106 C575,130 480,140 360,140 C260,140 130,138 0,166 Z" fill="#7aaed8"/>
    <path d="M0,174 C130,144 260,146 360,146 C480,146 575,136 620,114 L620,354 L0,354 Z" fill="url(#contactFill)"/>
  </svg>

  <div class="contact-brand">RW Holloway LLC</div>

  <div class="contact-details">
    <p class="person-name">Dane Corwell</p>
    <p class="person-role">Co-Founder</p>
    <p class="address">1840 W. Ridge Avenue<br>Suite 204 Alamo 12</p>
    <p class="contact-line">
      <svg viewBox="0 0 16 16"><path d="M3 1.5l3 .5 1 3-2 1.5a9 9 0 0 0 4.5 4.5L11 9l3 1 .5 3-1.5 1.5C7 14.5 1.5 9 1.5 3z" fill="#fff"/></svg>
      210-555-0148
    </p>
    <p class="contact-line">
      <svg viewBox="0 0 16 16"><path d="M1 6c2-3 12-3 14 0l-1 2-3-1V5H5v2L2 8z M4 9h8l2 5H2z" fill="#fff"/></svg>
      210-555-0176
    </p>
    <p class="contact-line">
      <svg viewBox="0 0 16 16"><rect x="1" y="3" width="14" height="10" rx="1" fill="#fff"/><path d="M1.5 3.5 8 9l6.5-5.5" fill="none" stroke="#b6a797" stroke-width="1.2"/></svg>
      info@rwhollowayllc
    </p>
    <p class="contact-line">
      <svg viewBox="0 0 16 16"><circle cx="8" cy="8" r="6.5" fill="none" stroke="#fff" stroke-width="1.4"/><path d="M1.5 8h13M8 1.5c-3 3.5-3 9.5 0 13M8 1.5c3 3.5 3 9.5 0 13" fill="none" stroke="#fff" stroke-width="1.1"/></svg>
      www.rwholloway.com
    </p>
  </div>
</section>

</body>
</html>
```